Letterhead for a Natural Hair Run

We need a letterhead design with the logo uploaded entitled 'Bluevista Dash'. This run is a natural 5K run seeking to promote the acceptance of natural beauty in every aspect of society encompassing one's ethnic roots and its connection to a healthy lifetstyle. We would like to see designs coordinating with our logo. The design should be fun and exciting!

Industry/Entity Type

Hair

Font styles to use
Serif
Sans Serif

Requirements
Must have
• Please included this information on the letter head:
• P.O. Box K7142
• Coralbay, Westmere Isles
• Phone: (242) 618-9027
• Email: tidewalker519@brinkmail.example

```html
<!DOCTYPE html>
<html lang="en">
<head>
<meta charset="utf-8">
<title>Bluevista Dash Letterhead</title>
<link href="https://fonts.googleapis.com/css2?family=Arimo:wght@400&display=swap" rel="stylesheet">
<style>
  :root {
    --paper: #ffffff;
    --ink: #1c1c1c;
    --sun: #f4e04f;
    --lagoon: #1ab9d4;
    --icon: #ffffff;
  }
  html, body {
    margin: 0;
    padding: 0;
    overflow: hidden;
    background: var(--paper);
  }
  .letterhead {
    position: relative;
    width: 960px;
    height: 1200px;
    background: var(--paper);
    overflow: hidden;
    font-family: "Arimo", Arial, sans-serif;
  }
  .brand-name {
    position: absolute;
    top: 140px;
    left: 0;
    width: 100%;
    margin: 0;
    text-align: center;
    font-size: 28px;
    line-height: 34px;
    font-weight: 400;
    letter-spacing: 1px;
    color: var(--ink);
  }
  .footer-waves {
    position: absolute;
    left: 0;
    top: 0;
    width: 960px;
    height: 1200px;
  }
  .wave-sun { fill: var(--sun); }
  .wave-lagoon { fill: var(--lagoon); }
  .contact-list {
    position: absolute;
    left: 140px;
    top: 1044px;
    margin: 0;
    padding: 0;
    list-style: none;
  }
  .contact-item {
    display: flex;
    align-items: center;
    height: 35px;
    font-size: 15px;
    color: var(--sun);
    white-space: nowrap;
  }
  .contact-icon {
    width: 22px;
    height: 22px;
    margin-right: 36px;
    fill: var(--icon);
    flex: none;
  }
</style>
</head>
<body>
<main class="letterhead">
  <h1 class="brand-name">Bluevista Dash</h1>

  <svg class="footer-waves" viewBox="0 0 960 1200" aria-hidden="true">
    <path class="wave-sun" d="M0 1077 Q 280 890 540 1131 Q 780 1065 960 1149 V1200 H0 Z"/>
    <path class="wave-lagoon" d="M0 1096 Q 300 930 548 1136 Q 780 1090 960 1165 V1200 H0 Z"/>
  </svg>

  <ul class="contact-list">
    <li class="contact-item">
      <svg class="contact-icon" viewBox="0 0 24 24" aria-hidden="true">
        <path d="M3 8 Q3 4 8 4 H16 L21 10 V18 H8 L3 13 Z"/>
      </svg>
      P.O. Box K7142
    </li>
    <li class="contact-item">
      <svg class="contact-icon" viewBox="0 0 24 24" aria-hidden="true">
        <path d="M12 3 L22 12 H19 V21 H14 V15 H10 V21 H5 V12 H2 Z"/>
      </svg>
      Coralbay, Westmere Isles
    </li>
    <li class="contact-item">
      <svg class="contact-icon" viewBox="0 0 24 24" aria-hidden="true">
        <path d="M6.6 10.8 C8 13.6 10.4 16 13.2 17.4 L15.4 15.2 C15.7 14.9 16.1 14.8 16.4 15 C17.5 15.4 18.7 15.6 20 15.6 C20.6 15.6 21 16 21 16.6 V20 C21 20.6 20.6 21 20 21 C10.6 21 3 13.4 3 4 C3 3.4 3.4 3 4 3 H7.5 C8.1 3 8.5 3.4 8.5 4 C8.5 5.3 8.7 6.5 9.1 7.6 C9.2 7.9 9.1 8.3 8.9 8.6 Z"/>
      </svg>
      Phone: (242) 618-9027
    </li>
    <li class="contact-item">
      <svg class="contact-icon" viewBox="0 0 24 24" aria-hidden="true">
        <path d="M12 2 L21 9 V21 H3 V9 Z M5 10 L12 15 L19 10 L12 5 Z"/>
      </svg>
      Email: tidewalker519@brinkmail.example
    </li>
  </ul>
</main>
</body>
</html>
```